New Business Card for Web Design/Internet Marketing Company

Looking for a great looking new business card. We are a 10 year old web design, internet marketing and website management company that works mostly with small businesses.

Our new card needs to better match the colors and style of our website, be bold, extremely usable and slightly edgy.

Target Market(s)

Small/Medium businesses that have websites

Industry/Entity Type

Internet

Requirements
Must have
• Front and back design, full color, rounded corners please

Must use the colors/style of our website (JPG provided)

INFO FOR CARDS (as readable as possible please)
Mark Lenner
President/CEO
mark@trelvanmedia.example
Phone: 520-381-7459
Toll Free: 866-381-7459
Address: 4315 W. Calloway Ave. Ste. 140, Tucson, AZ 85792

THINGS I WANT TO PROMOTE (if there is room):
1. Our Website - www.trelvanmedia.example

2. Social Media
Twitter: @trelvanmedia
Facebook: www.facebook.com/trelvanmedia

3. Our Services
Web Design
Internet Marketing
Website Management

```html
<!DOCTYPE html>
<html lang="en">
<head>
<meta charset="utf-8">
<title>Trelvan Media – Business Card, Front and Back</title>
<link rel="stylesheet" href="https://fonts.googleapis.com/css2?family=Source+Sans+3:wght@400;600;700&display=swap">
<style>
  :root {
    --page-bg: #e8e4de;
    --brand-blue: #1b93cf;
    --brand-orange: #f08a2c;
    --ink-grey: #4a4a4a;
    --white: #ffffff;
    --card-shadow: 0 2px 6px rgba(0,0,0,0.18);
  }
  * { box-sizing: border-box; margin: 0; padding: 0; }
  html, body {
    width: 1200px; height: 402px; overflow: hidden;
    background: var(--page-bg);
    font-family: "Source Sans 3", "Segoe UI", sans-serif;
  }
  .canvas { position: relative; width: 1200px; height: 402px; }

  .card {
    position: absolute; top: 51px;
    width: 512px; height: 292px;
    border-radius: 6px; overflow: hidden;
    box-shadow: var(--card-shadow);
  }
  .card--front { left: 58px; background: var(--white); }
  .card--back { left: 629px; background: var(--brand-blue); }

  .front-waves { position: absolute; inset: 0; }

  .wordmark { position: absolute; display: flex; align-items: center; gap: 10px; }
  .wordmark__dot { border-radius: 50%; flex: none; }
  .wordmark__name { font-weight: 700; line-height: 1; white-space: nowrap; }

  .card--front .wordmark { left: 36px; top: 90px; }
  .card--front .wordmark__dot { width: 22px; height: 22px; background: var(--brand-orange); }
  .card--front .wordmark__name { font-size: 31px; color: var(--brand-blue); }

  .person { position: absolute; right: 40px; top: 44px; text-align: right; color: var(--brand-blue); }
  .person__name { font-size: 18px; font-weight: 600; line-height: 1.1; }
  .person__title { font-size: 12.5px; line-height: 1.2; }

  .contact-list {
    position: absolute; right: 40px; top: 118px;
    list-style: none; text-align: right;
    font-size: 13px; color: var(--ink-grey); line-height: 18px;
  }
  .contact-list li { display: flex; justify-content: flex-end; align-items: center; gap: 5px; }
  .contact-icon { width: 10px; height: 10px; flex: none; }

  .address {
    position: absolute; right: 56px; top: 252px;
    text-align: right; color: var(--white);
    font-size: 13px; line-height: 18px; font-style: normal;
  }

  .card--back .wordmark { left: 28px; top: 132px; }
  .card--back .wordmark__dot { width: 24px; height: 24px; background: var(--white); }
  .card--back .wordmark__name { font-size: 29px; color: var(--white); }

  .social { position: absolute; left: 290px; top: 36px; list-style: none; color: var(--white); font-size: 16.5px; line-height: 23px; }
  .social li { display: flex; align-items: center; gap: 10px; }
  .social__mark { width: 15px; height: 15px; background: rgba(255,255,255,0.85); border-radius: 2px; }

  .services { position: absolute; left: 290px; top: 114px; color: var(--white); }
  .services__title { font-size: 25px; font-weight: 600; margin-bottom: 14px; }
  .services__list { list-style: none; font-size: 22px; line-height: 31px; }
</style>
</head>
<body>
<main class="canvas">

  <section class="card card--front" aria-label="Business card front">
    <svg class="front-waves" viewBox="0 0 512 292" width="512" height="292" aria-hidden="true">
      <path d="M0,150 C30,235 120,262 220,238 C320,214 410,200 460,220 C495,236 508,262 512,292 L0,292 Z" fill="var(--brand-blue)"/>
      <path d="M0,192 C60,252 150,258 240,234 C330,210 430,196 520,296" fill="none" stroke="var(--white)" stroke-width="16"/>
      <path d="M0,192 C60,252 150,258 240,234 C330,210 430,196 520,296" fill="none" stroke="var(--brand-orange)" stroke-width="8"/>
    </svg>

    <div class="wordmark">
      <span class="wordmark__dot"></span>
      <span class="wordmark__name">Trelvan Media</span>
    </div>

    <div class="person">
      <p class="person__name">Mark Lenner</p>
      <p class="person__title">President/CEO</p>
    </div>

    <ul class="contact-list">
      <li>520-381-7459
        <svg class="contact-icon" viewBox="0 0 10 10"><circle cx="5" cy="5" r="5" fill="var(--brand-blue)"/><path d="M3,2.5 L4.3,2.5 L4.8,4 L4,4.6 Q4.8,6 5.9,6.3 L6.5,5.6 L7.7,6.1 L7.5,7.4 Q4,7.6 2.6,3.4 Z" fill="var(--white)"/></svg>
      </li>
      <li>866-381-7459
        <svg class="contact-icon" viewBox="0 0 10 10"><circle cx="5" cy="5" r="5" fill="var(--brand-blue)"/><path d="M3,2.5 L4.3,2.5 L4.8,4 L4,4.6 Q4.8,6 5.9,6.3 L6.5,5.6 L7.7,6.1 L7.5,7.4 Q4,7.6 2.6,3.4 Z" fill="var(--white)"/></svg>
      </li>
      <li>mark@trelvanmedia.example
        <svg class="contact-icon" viewBox="0 0 10 10"><rect x="0.5" y="2" width="9" height="6.5" fill="var(--brand-blue)"/><path d="M0.5,2 L5,5.6 L9.5,2" fill="none" stroke="var(--white)" stroke-width="0.9"/></svg>
      </li>
      <li>www.trelvanmedia.example
        <svg class="contact-icon" viewBox="0 0 10 10"><circle cx="5" cy="5" r="4.4" fill="var(--brand-blue)"/><g fill="none" stroke="var(--white)" stroke-width="0.7"><ellipse cx="5" cy="5" rx="1.8" ry="4.2"/><path d="M0.8,5 H9.2 M1.5,3 H8.5 M1.5,7 H8.5"/></g></svg>
      </li>
    </ul>

    <address class="address">
      4315 W. Calloway Ave. Ste. 140<br>
      Tucson, AZ 85792
    </address>
  </section>

  <section class="card card--back" aria-label="Business card back">
    <div class="wordmark">
      <span class="wordmark__dot"></span>
      <span class="wordmark__name">Trelvan Media</span>
    </div>

    <ul class="social">
      <li><span class="social__mark" aria-hidden="true"></span>@trelvanmedia</li>
      <li><span class="social__mark" aria-hidden="true"></span>trelvanmedia</li>
    </ul>

    <div class="services">
      <h2 class="services__title">Our Services</h2>
      <ul class="services__list">
        <li>Web Design</li>
        <li>Internet Marketing</li>
        <li>Website Management</li>
      </ul>
    </div>
  </section>

</main>
</body>
</html>
```